Business card for Crestline Bathrooms

Please design a business card for our bathroom renovation business. You can use my existing logo, but if you have an idea to modernize it, I would like to see it. Please see attached files first. I would like to use the blue and the orange theme. I like the concept of using the shower head in the logo. Please find following a design (or two) that I have been trying to create with my limited resources. That design was for a sign, but I was going to adopt it and use it as a business card as well. I like the concept of the water splash but I don’t think it “flows” nicely together with the logo. Another thought is that maybe creating the logo out of water splash could work and have a dramatic effect (like the water text and the butterfly picture attached with similar background instead of white). If the above doesn’t work I would like to see a modern simplified design. One of the attached files named as the unwanted business card has all the details that I want included in the business card. Please note that it is two sided.
Updates

I am very thankful for the designs that I have received, but they are very similar and only a couple of attempts to do something with the water splash as per my original brief. Modernizing the logo and having it made out of out of water splash with the orange as color accent could work and have a dramatic effect (like the water text and the butterfly picture attached with similar background instead of white). Please do not use the butterfly itself! This is just an example that images can be created out of water splash.

Contact Information for Business Card

all the details are on the unwonted business card file included

Colors
3176b5

Requirements
Nice to have
• Copied from the brief:
• ... maybe creating the logo out of water splash could work and have a dramatic effect (like the water text and the butterfly picture attached with similar background instead of white). Please do not use the butterfly itself!
Should not have
• I am getting designs with a butterfly. The butterfly picture was an example of creating something from a water splash. The butterfly itself has no association with anything other than the concept of creating a logo out of water splash. Sorry, I thought I was clear in the brief.

```html
<!DOCTYPE html>
<html lang="en">
<head>
<meta charset="utf-8">
<title>Crestline Bathrooms – Business Card</title>
<link href="https://fonts.googleapis.com/css2?family=Montserrat:wght@600;700;800&family=Oswald:wght@600&display=swap" rel="stylesheet">
<style>
  :root {
    --stage: #34434d;
    --water-deep: #1f4f8f;
    --water-mid: #3176b5;
    --water-light: #8fb4e6;
    --accent: #f0612a;
    --band: #14181d;
    --band-navy: #15253a;
    --ink-light: #ffffff;
    --logo-ink: #1d2a4e;
  }
  * { box-sizing: border-box; margin: 0; padding: 0; }
  html, body { width: 1200px; height: 1200px; overflow: hidden; }
  body {
    background: var(--stage);
    font-family: "Montserrat", sans-serif;
    display: flex;
    flex-direction: column;
    align-items: center;
    justify-content: center;
    gap: 60px;
  }
  .card {
    position: relative;
    width: 1000px;
    height: 500px;
    overflow: hidden;
    box-shadow: 0 10px 30px rgba(0,0,0,.35);
  }
  .card__photo {
    position: absolute;
    inset: 0;
  }
  .card--front .card__photo {
    background:
      radial-gradient(ellipse 60% 35% at 50% 60%, rgba(200,220,255,.45), transparent 70%),
      radial-gradient(ellipse 80% 50% at 30% 80%, rgba(120,160,230,.5), transparent 70%),
      linear-gradient(180deg, var(--water-mid) 0%, #4a7fd0 45%, var(--water-deep) 100%);
  }
  .card--back .card__photo {
    background:
      radial-gradient(ellipse 55% 30% at 50% 85%, rgba(200,220,255,.5), transparent 70%),
      linear-gradient(180deg, #2a6396 0%, #336fa8 50%, #4f82cf 70%, var(--water-deep) 100%);
  }

  /* brand name */
  .brand {
    position: absolute;
    display: flex;
    align-items: center;
    gap: 14px;
    font-weight: 800;
    color: var(--logo-ink);
    white-space: nowrap;
  }
  .brand__dot {
    width: 34px; height: 34px;
    border-radius: 50%;
    background: var(--accent);
  }
  .card--front .brand { top: 70px; left: 50%; transform: translateX(-50%); font-size: 46px; }
  .card--back .brand { top: 110px; left: 70px; font-size: 44px; }

  /* front */
  .front__band {
    position: absolute;
    left: 0; right: 0; top: 190px;
    height: 50px;
    background: var(--band);
    display: flex; align-items: center; justify-content: center;
    color: var(--accent);
    font-weight: 800;
    font-size: 32px;
    letter-spacing: .5px;
  }
  .front__tagline {
    position: absolute;
    top: 335px; left: 50%;
    transform: translateX(-50%);
    background: var(--band);
    color: var(--accent);
    font-weight: 700;
    font-size: 22px;
    padding: 7px 26px;
    border-radius: 22px;
    white-space: nowrap;
  }

  /* back */
  .back__service {
    position: absolute;
    right: 60px; top: 175px;
    font-family: "Oswald", sans-serif;
    font-weight: 600;
    color: var(--accent);
    font-size: 46px;
    transform: scaleY(1.1);
  }
  .back__band {
    position: absolute;
    left: 0; right: 0; top: 250px;
    height: 38px;
    background: var(--band-navy);
  }
  .back__band-text {
    position: absolute;
    right: 150px; top: 50%;
    transform: translateY(-50%);
    color: var(--ink-light);
    font-weight: 700;
    font-size: 21px;
  }
  .contact {
    position: absolute;
    left: 540px; top: 318px;
    list-style: none;
    display: flex; flex-direction: column; gap: 18px;
  }
  .contact__item {
    display: flex; align-items: center; gap: 16px;
    color: var(--ink-light);
    font-weight: 700;
    font-size: 26px;
    text-shadow: 0 2px 3px rgba(0,0,0,.5);
  }
  .contact__item--phone { font-size: 30px; letter-spacing: 1px; }
  .contact__icon { width: 48px; height: 52px; flex: none; }
</style>
</head>
<body>

  <section class="card card--front" aria-label="Business card front">
    <div class="card__photo" role="img" aria-label="Blue water ripple photograph"></div>
    <div class="brand"><span class="brand__dot"></span>Crestline Bathrooms</div>
    <div class="front__band">BATHROOM RENOVATION</div>
    <div class="front__tagline">From Concept to Completion</div>
  </section>

  <section class="card card--back" aria-label="Business card back">
    <div class="card__photo" role="img" aria-label="Blue water splash photograph with droplets"></div>
    <div class="brand"><span class="brand__dot"></span>Crestline Bathrooms</div>
    <div class="back__service">BATHROOM RENOVATIONS</div>
    <div class="back__band"><span class="back__band-text">Professional Service</span></div>
    <ul class="contact">
      <li class="contact__item contact__item--phone">
        <svg class="contact__icon" viewBox="0 0 48 52" aria-hidden="true">
          <polygon points="24,1 46,13.5 46,38.5 24,51 2,38.5 2,13.5" fill="#111"/>
          <rect x="14" y="14" width="20" height="24" rx="3" fill="none" stroke="var(--accent)" stroke-width="2"/>
          <path d="M19 19 q-2 4 2 9 q4 5 8 5 l2-3 -4-3 -2 2 q-3-2-4-5 l2-2 -2-4z" fill="var(--accent)"/>
        </svg>
        0400 555 018
      </li>
      <li class="contact__item">
        <svg class="contact__icon" viewBox="0 0 48 52" aria-hidden="true">
          <polygon points="24,1 46,13.5 46,38.5 24,51 2,38.5 2,13.5" fill="#111"/>
          <g fill="none" stroke="var(--accent)" stroke-width="2">
            <circle cx="24" cy="26" r="12"/>
            <ellipse cx="24" cy="26" rx="5" ry="12"/>
            <line x1="12" y1="26" x2="36" y2="26"/>
            <line x1="14" y1="20" x2="34" y2="20"/>
            <line x1="14" y1="32" x2="34" y2="32"/>
          </g>
        </svg>
        crestlinebathrooms.com.au
      </li>
    </ul>
  </section>

</body>
</html>
```